Holiday Rental Company Flyer Design (DL not A5)

Note from Brandloom Administration: The category sizing selected is A5, however the project requires DL sized artwork. Please refer to the DL template link below while the 'Special Requirements' are updated accordingly.

Project Brief:
We need a double sided DL flyer designed for an up market Holiday Rental Company that portrays a personalised approach to property management. These are to be used for letter box drops to homes we're specifically targeting so the design should be modern, complimentary colour palette, uncluttered & visually appealing.

Please Download the DL Template from Quillora here: http://www.quillora.com.au/ql/ns/propath/UploadResources.aspx?selectedTab=0?pfid=KMT&pf_id=KMT&xnav=easypath-upload-image#Templates

Target Market(s)

Wealthy Home Owners

Industry/Entity Type

It Company

Other font styles liked:
• Avant Garde Extra Light & Demi

Colors
33b8a4

Requirements
Must have
• DL Flyer sizes (210mm width x 99mm width, plus 3mm bleed)
• Front: Logo, Main Image & Grab
• Back: Contact Details & Brief Description of our business
• Images: Ideally the main image should be the house with the pool but alternatively a lifestyle images could also be used.
Nice to have
• A creative designer!
Should not have
• Clutter & busy designs

```html
<!DOCTYPE html>
<html lang="en">
<head>
<meta charset="utf-8">
<title>Harbourline Stays – DL Flyer</title>
<link rel="stylesheet" href="https://fonts.googleapis.com/css2?family=Anton&family=Lato:ital,wght@0,400;0,700;1,400&family=Raleway:wght@200;300&display=swap">
<style>
  :root{
    --navy:#1c1a4f;
    --teal:#33b8a4;
    --white:#ffffff;
    --stage:#2b2b2d;
  }
  *{box-sizing:border-box;margin:0;padding:0}
  html,body{width:1200px;height:1051px;overflow:hidden}
  body{background:var(--stage);position:relative;font-family:'Lato',sans-serif}

  .flyer{position:absolute;top:130px;width:540px;height:790px;overflow:hidden;background:var(--navy);color:var(--white)}
  .flyer--back{left:40px}
  .flyer--front{left:620px}

  /* back side */
  .back-shapes{position:absolute;inset:0}
  .back-copy{position:absolute;left:46px;right:40px;top:240px}
  .back-heading{font-family:'Raleway',sans-serif;font-weight:200;font-size:46px;line-height:1;letter-spacing:1px;text-transform:uppercase;margin-bottom:20px}
  .back-text{font-size:15.5px;line-height:1.4;margin-bottom:14px}
  .back-list{list-style:none;font-size:15.5px;line-height:1.45}
  .back-contact{position:absolute;left:0;right:0;top:632px;text-align:center}
  .contact-intro{font-style:italic;font-size:15px;line-height:1.35;margin-bottom:6px}
  .contact-phone{font-weight:700;font-size:42px;letter-spacing:1px;line-height:1.1}
  .contact-address{font-weight:700;font-size:15px;margin:4px 0 6px}
  .contact-email{font-size:17px}

  /* front side */
  .front-frame{position:absolute;left:38px;top:40px;width:464px;height:700px;border:1.5px solid var(--white)}
  .logo-block{position:absolute;left:30px;top:34px;width:180px;height:126px;background:var(--teal);display:flex;flex-direction:column;align-items:center;justify-content:center;gap:12px}
  .logo-name{font-family:'Raleway',sans-serif;font-weight:300;font-size:22px;letter-spacing:2px;line-height:1.1;text-align:center;text-transform:uppercase}
  .logo-mark{width:14px;height:14px;border:1.5px solid var(--white);border-radius:50%}
  .headline{position:absolute;right:56px;top:195px;text-align:right}
  .headline-main{font-family:'Anton',sans-serif;font-size:106px;line-height:1;letter-spacing:1px}
  .headline-sub{font-family:'Raleway',sans-serif;font-weight:200;font-size:37px;line-height:1.08;letter-spacing:1px;margin-top:4px}
  .front-photo{position:absolute;left:0;right:0;top:370px;bottom:0}
  .web-tab{position:absolute;right:38px;top:706px;background:var(--white);color:var(--teal);font-size:15px;letter-spacing:1px;padding:6px 16px 6px 28px}
</style>
</head>
<body>

<section class="flyer flyer--back" aria-label="Flyer back">
  <svg class="back-shapes" width="540" height="790" viewBox="0 0 540 790">
    <defs>
      <linearGradient id="bathTone" x1="0" y1="0" x2="1" y2="1"><stop offset="0" stop-color="#d9d7d2"/><stop offset="1" stop-color="#9c9a95"/></linearGradient>
      <linearGradient id="flowerTone" x1="0" y1="0" x2="1" y2="1"><stop offset="0" stop-color="#8a7a6a"/><stop offset="1" stop-color="#b0483a"/></linearGradient>
      <linearGradient id="bedTone" x1="0" y1="0" x2="1" y2="1"><stop offset="0" stop-color="#c9a27a"/><stop offset="1" stop-color="#d6c14a"/></linearGradient>
    </defs>
    <polygon points="0,40 540,40 540,210 0,210" fill="#ffffff"/>
    <g role="img" aria-label="Photo of a bathroom basin">
      <rect x="0" y="48" width="180" height="162" fill="url(#bathTone)"/>
    </g>
    <g role="img" aria-label="Photo of a flower arrangement in a living room">
      <rect x="183" y="48" width="177" height="162" fill="url(#flowerTone)"/>
    </g>
    <g role="img" aria-label="Photo of a bed with yellow cushions">
      <rect x="363" y="48" width="177" height="162" fill="url(#bedTone)"/>
    </g>
    <path d="M0,214 L540,214 L540,578 Q300,628 0,610 Z" fill="var(--teal)"/>
    <path d="M0,214 L540,214" stroke="#ffffff" stroke-width="6"/>
    <path d="M0,614 Q300,632 540,582" stroke="#ffffff" stroke-width="3" fill="none"/>
  </svg>

  <div class="back-copy">
    <h2 class="back-heading">What we do<br>differently!</h2>
    <p class="back-text">Rather than relying upon a key safe or a central pick-up destination, a ‘Harbourline Stays’ staff member will greet guests upon arrival.</p>
    <p class="back-text">Our ‘Meet &amp; Greet’ service provides home owners with an increased level of Security and also allows us to:</p>
    <ul class="back-list">
      <li>Prepare the home for their arrival (lights, heaters, music etc.)</li>
      <li>Establish a rapport &amp; help facilitate future bookings</li>
      <li>Reiterate their responsibilities to ensure the return of their bond</li>
    </ul>
  </div>

  <div class="back-contact">
    <p class="contact-intro">If you’d like to know what your property could achieve or<br>require additional information, please contact us on:</p>
    <p class="contact-phone">(03)5971 2260</p>
    <p class="contact-address">PO Box 48, Tidewater Victoria 3990</p>
    <p class="contact-email">email: stay@harbourlinestays.com.au</p>
  </div>
</section>

<section class="flyer flyer--front" aria-label="Flyer front">
  <svg class="front-photo" width="540" height="420" viewBox="0 0 540 420" role="img" aria-label="Photo of a modern house at night with a lit swimming pool">
    <defs>
      <linearGradient id="nightTone" x1="0" y1="0" x2="0" y2="1">
        <stop offset="0" stop-color="#1c1a4f"/>
        <stop offset="0.45" stop-color="#5a4a6e"/>
        <stop offset="0.7" stop-color="#b08a5a"/>
        <stop offset="0.85" stop-color="#2f7fd8"/>
        <stop offset="1" stop-color="#3aa0f0"/>
      </linearGradient>
    </defs>
    <rect width="540" height="420" fill="url(#nightTone)"/>
  </svg>

  <div class="front-frame"></div>

  <div class="logo-block">
    <span class="logo-name">Harbourline<br>Stays</span>
    <span class="logo-mark"></span>
  </div>

  <div class="headline">
    <h1 class="headline-main">HOLIDAY</h1>
    <p class="headline-sub">RENTAL MANAGEMENT<br>WITH A DIFFERENCE</p>
  </div>

  <div class="web-tab">harbourlinestays.com.au</div>
</section>

</body>
</html>
```